A private security company called "Tavron Security Services Ltd"

Hello everybody,

We need a web page for a company based in NZ. It is mainly an informative website so it would be wonderful if the designer puts their absolute best into making it a website that I would really appreciate. The website needs to show professionalism and also needs to make our web surfers find the information they need in a click. the company's colour is black and silver, and if those two colours could be integrated into the website it would be absolutely lovely. Please do contact me for any information.

Sincerely,
Dorian Vaskel

Industry/Entity Type

Security

```html
<!DOCTYPE html>
<html lang="en">
<head>
<meta charset="utf-8">
<title>Tavron Security Services Ltd</title>
<link rel="stylesheet" href="https://fonts.googleapis.com/css2?family=Montserrat:wght@300;400;600;700&family=Open+Sans:wght@300;400;600&family=PT+Sans&display=swap">
<style>
  :root {
    --night: #0a0f24;
    --night-mid: #1a2550;
    --night-glow: #3a4672;
    --black: #050505;
    --ink: #1b1b1b;
    --silver: #e8e8e8;
    --silver-dark: #c9c9c9;
    --grey-text: #5a5a5a;
    --footer-text: #9a9a9a;
    --line: #2a2a2a;
    --white: #fff;
    --button-dark: #0f1628;
    --accent: #1f8ea3;
  }
  * { box-sizing: border-box; margin: 0; padding: 0; }
  html, body { width: 1192px; height: 1200px; overflow: hidden; background: var(--white); }
  body { position: relative; font-family: "Open Sans", Arial, sans-serif; color: var(--ink); }

  /* Hero */
  .hero {
    position: absolute; left: 0; top: 0; width: 1192px; height: 561px;
    background: radial-gradient(ellipse 380px 300px at 820px 280px, var(--night-glow), transparent 70%),
                linear-gradient(180deg, #05070f 0%, var(--night) 40%, var(--night-mid) 100%);
    color: var(--white);
  }
  .hero-shadow { position: absolute; left: 0; top: 561px; width: 1192px; height: 22px;
    background: linear-gradient(180deg, #cfcfcf, #fff); }
  .brand-mark { position: absolute; left: 160px; top: 30px; width: 50px; height: 50px;
    border: 2px solid var(--white); border-radius: 50%; }
  .brand { position: absolute; left: 110px; top: 92px; width: 200px;
    font-family: "Montserrat", sans-serif; font-weight: 600; font-size: 13px; line-height: 17px;
    color: var(--white); letter-spacing: 0.4px; }
  .call { position: absolute; right: 102px; top: 55px; font-family: "PT Sans", sans-serif; font-size: 24px; }
  .nav { position: absolute; top: 96px; left: 528px; display: flex; gap: 5px; }
  .nav a { display: block; height: 26px; background: var(--white); color: #111;
    font-family: Arial, Helvetica, sans-serif; font-size: 13.5px; line-height: 26px; text-decoration: none;
    text-align: center; border-radius: 2px; white-space: nowrap; }
  .hero-title { position: absolute; left: 110px; top: 228px; font-family: "Montserrat", sans-serif;
    font-size: 29px; font-weight: 300; letter-spacing: -0.8px; white-space: nowrap; }
  .hero-title strong { font-weight: 600; }
  .hero-copy { position: absolute; left: 110px; top: 282px; width: 620px; font-family: "Montserrat", sans-serif;
    font-size: 12px; line-height: 16.5px; letter-spacing: -0.2px; }
  .hero-copy p + p { margin-top: 16px; }
  .cta { position: absolute; left: 110px; top: 403px; width: 174px; height: 32px;
    background: linear-gradient(180deg, #fff, #dcdcdc); border-radius: 2px; display: flex; align-items: center; }
  .cta .chev { width: 30px; height: 32px; border-right: 1px solid #bbb; display: flex; align-items: center; justify-content: center; }
  .cta span { margin-left: 11px; font-family: "Montserrat", sans-serif; font-weight: 700; font-size: 13px; color: #16213d; white-space: nowrap; }
  .slider-arrows { position: absolute; left: 110px; top: 525px; width: 45px; height: 23px; background: var(--white);
    border-radius: 2px; display: flex; }
  .slider-arrows div { flex: 1; display: flex; align-items: center; justify-content: center; }
  .slider-arrows div + div { border-left: 1px solid #999; }
  .camera-photo { position: absolute; left: 890px; top: 150px; width: 302px; height: 411px;
    background: linear-gradient(160deg, #e4e4e0 0%, #c8c9cb 45%, #8e93a6 80%, transparent 100%);
    border-radius: 40px 0 0 0; opacity: 0.9; }

  /* Services */
  .section-title { position: absolute; left: 125px; top: 606px; width: 942px; height: 42px;
    background: #f2f2f2; border: 1px solid var(--silver-dark); text-align: center;
    font-size: 21px; font-weight: 300; line-height: 40px; color: #222; }
  .section-title strong { font-weight: 600; }
  .service { position: absolute; top: 663px; width: 300px; }
  .service-photo { width: 128px; height: 83px; }
  .service-name { position: absolute; left: 138px; font-size: 19.5px; line-height: 24px; color: #333; font-weight: 400; }
  .service-copy { margin-top: 21px; font-size: 12px; line-height: 16px; color: var(--grey-text); font-weight: 400; width: 282px; letter-spacing: -0.2px; }
  .learn { margin-top: 11px; width: 127px; height: 26px; background: linear-gradient(90deg, var(--button-dark) 70%, #2a3350);
    border-radius: 2px; color: var(--white); font-size: 12.5px; font-weight: 600; line-height: 26px; padding-left: 9px; position: relative; }
  .learn svg { position: absolute; right: 12px; top: 8px; }

  /* Footer */
  .footer { position: absolute; left: 0; top: 940px; width: 1192px; height: 260px; background: var(--black); color: var(--footer-text); }
  .footer h3 { position: absolute; top: 33px; font-size: 15px; font-weight: 400; color: var(--white); width: 232px;
    padding-bottom: 10px; border-bottom: 1px solid var(--line); }
  .footer .text { position: absolute; top: 86px; font-size: 13.5px; line-height: 20px; font-weight: 300; white-space: nowrap; }
  .socials { position: absolute; left: 428px; top: 113px; display: flex; gap: 5px; }
  .socials span { width: 24px; height: 24px; background: var(--silver-dark); border-radius: 3px; display: block; }
  .subscribe { position: absolute; left: 812px; top: 155px; display: flex; }
  .subscribe .field { width: 166px; height: 36px; background: var(--white); color: #999; font-size: 13.5px; line-height: 36px; padding-left: 10px; font-weight: 300; }
  .subscribe .ok { width: 49px; height: 36px; border: 1px solid var(--silver); color: var(--white); font-size: 16px; line-height: 34px; text-align: center; }
  .footer-rule { position: absolute; left: 128px; top: 221px; width: 950px; border-top: 1px solid #1e1e1e; }
  .legal { position: absolute; top: 238px; width: 1192px; text-align: center; font-size: 12.5px; color: #ddd; }
</style>
</head>
<body>
  <header class="hero">
    <div class="brand-mark"></div>
    <div class="brand">Tavron<br>Security Services Ltd.</div>
    <div class="call">Call: 021 555 0184</div>
    <nav class="nav">
      <a href="#" style="width:84px">HOME</a>
      <a href="#" style="width:94px">About Us</a>
      <a href="#" style="width:124px">Security System</a>
      <a href="#" style="width:148px">Specialized Security</a>
      <a href="#" style="width:88px">Contact Us</a>
    </nav>
    <h1 class="hero-title"><strong>Newzealand’s Best</strong> Security Company</h1>
    <div class="hero-copy">
      <p>It is a long established fact that a reader will be distracted by the readable content of a page when looking at its layout. The point of using Lorem Ipsum is that it has a more-or-less normal distribution of lettersas opposed to using 'Content here, content here', making it look like readable English.</p>
      <p>Many desktop publishing packages and web page editors now use Lorem Ipsum as their default model text, and a search.</p>
    </div>
    <div class="cta">
      <div class="chev"><svg width="7" height="10" viewBox="0 0 7 10"><path d="M1 1l4 4-4 4" fill="none" stroke="var(--accent)" stroke-width="2"/></svg></div>
      <span>FIND OUT MORE</span>
    </div>
    <div class="camera-photo" role="img" aria-label="White CCTV security camera on a curved mount against a night sky"></div>
    <div class="slider-arrows">
      <div><svg width="6" height="8"><path d="M6 0v8L0 4z" fill="#000"/></svg></div>
      <div><svg width="6" height="8"><path d="M0 0v8l6-4z" fill="#000"/></svg></div>
    </div>
  </header>
  <div class="hero-shadow"></div>

  <h2 class="section-title">WE <strong>SECURE</strong> YOUR LIFE</h2>

  <article class="service" style="left:127px">
    <div class="service-photo" role="img" aria-label="Security cameras on a pole against a blue sky" style="background:linear-gradient(180deg,#6f8fb8,#a9b9c9 70%,#5e6466)"></div>
    <h3 class="service-name" style="top:19px">Security<br>Camera</h3>
    <p class="service-copy">It is a long established fact that a reader will be distracted by the readable content of a page when looking at its layout. The point of using Lorem Ipsum is that it has a more-or-less normal distribution of lettersas</p>
    <div class="learn">Learn more<svg width="7" height="10"><path d="M1 1l4 4-4 4" fill="none" stroke="#fff" stroke-width="1.5"/></svg></div>
  </article>

  <article class="service" style="left:440px">
    <div class="service-photo" role="img" aria-label="Fixed camera overlooking a city skyline" style="background:linear-gradient(180deg,#8fb3dd,#c8d8ea 60%,#6b7a8c)"></div>
    <h3 class="service-name" style="top:7px">Fixed<br>Camera<br>System</h3>
    <p class="service-copy">It is a long established fact that a reader will be distracted by the readable content of a page when looking at its layout. The point of using Lorem Ipsum is that it has a more-or-less normal distribution of lettersas</p>
    <div class="learn">Learn more<svg width="7" height="10"><path d="M1 1l4 4-4 4" fill="none" stroke="#fff" stroke-width="1.5"/></svg></div>
  </article>

  <article class="service" style="left:760px">
    <div class="service-photo" role="img" aria-label="Security officers at a monitoring control room" style="background:linear-gradient(180deg,#3a3f48,#7a6a5c 60%,#b8a48e)"></div>
    <h3 class="service-name" style="top:5px">Armed<br>Security<br>Officers</h3>
    <p class="service-copy">It is a long established fact that a reader will be distracted by the readable content of a page when looking at its layout. The point of using Lorem Ipsum is that it has a more-or-less normal distribution of lettersas</p>
    <div class="learn">Learn more<svg width="7" height="10"><path d="M1 1l4 4-4 4" fill="none" stroke="#fff" stroke-width="1.5"/></svg></div>
  </article>

  <footer class="footer">
    <h3 style="left:125px">CONTACT US</h3>
    <div class="text" style="left:127px">Newzealand, AK 1010<br>42 Harbour View Road<br>phone: +64 9 555 0172<br>Fax: +64 9 555 0173<br>Email: admin@tavronsecurity.co.nz</div>

    <h3 style="left:428px">GO SOCIAL</h3>
    <div class="text" style="left:428px">Stay in touch with us:</div>
    <div class="socials" aria-label="Social network links">
      <span role="img" aria-label="Social link 1"></span>
      <span role="img" aria-label="Social link 2"></span>
      <span role="img" aria-label="Social link 3"></span>
      <span role="img" aria-label="Social link 4"></span>
      <span role="img" aria-label="Social link 5"></span>
      <span role="img" aria-label="Social link 6"></span>
    </div>

    <h3 style="left:812px">SUBSCRIBE</h3>
    <div class="text" style="left:812px">Enter your e-mail below to subscribe to our<br>free newsletter.<br>We promise not to bother you often!</div>
    <div class="subscribe"><div class="field">Enter Email</div><div class="ok">OK</div></div>

    <div class="footer-rule"></div>
    <div class="legal">© Tavron Security Services 2014. Privacy Policy &nbsp;|&nbsp; Terms of Service</div>
  </footer>
</body>
</html>
```